Beacon Advisory Website

I currently have a website www.beaconadvisoryinc.com. We are a IT Consulting Company. Our website will pretty much tell out our services. I am looking to enhance my website and make it look more professional. Looking for very classy and Contemporary look and design for my website.

It Company

```html
<!DOCTYPE html>
<html lang="en">
<head>
<meta charset="utf-8">
<title>Beacon Advisory</title>
<link href="https://fonts.googleapis.com/css2?family=Montserrat:wght@500&family=Raleway:wght@400;500&family=Lato:ital,wght@0,400;1,400&display=swap" rel="stylesheet">
<style>
:root{
  --sky:#04a9e2;
  --navy:#1565a8;
  --button:#0f72b8;
  --ink:#2e2e2e;
  --body:#555;
  --white:#fff;
  --quote-bg:#e3f5fc;
  --quote-line:#3cb4e6;
  --frame:#86d3f0;
}
*{margin:0;padding:0;box-sizing:border-box}
html,body{width:880px;height:1200px;overflow:hidden}
body{position:relative;background:var(--white);font-family:'Lato',sans-serif;color:var(--body)}
.abs{position:absolute}

/* header */
.site-header{left:0;top:0;width:880px;height:76px;background:var(--white)}
.brand{left:58px;top:24px;display:flex;align-items:center;gap:8px}
.brand-mark{width:26px;height:26px;border-radius:50%;background:var(--navy)}
.brand-name{font-family:'Montserrat',sans-serif;font-weight:500;font-size:16px;color:var(--navy)}
.main-nav{left:271px;top:30px;display:flex;gap:20px;font-family:'Raleway',sans-serif;font-size:12.6px;color:#333;letter-spacing:.2px}
.main-nav .active{color:var(--sky)}

/* hero */
.band-sky{left:0;top:76px;width:880px;height:352px;background:var(--sky)}
.band-navy{left:0;top:428px;width:880px;height:305px;background:var(--navy)}
.hero{left:56px;top:122px;width:768px;height:360px;border:2px solid var(--white);overflow:hidden;
  background:linear-gradient(90deg,#f2f5f8 0%,#e4eaf0 40%,#c9d3dc 65%,#b9a79a 80%,#d9dee3 100%)}
.hero-title{left:32px;top:78px;font-family:'Montserrat',sans-serif;font-weight:500;font-size:49px;color:var(--ink);letter-spacing:-.5px}
.hero-sub{left:32px;top:134px;font-family:'Raleway',sans-serif;font-size:16px;color:#222}
.hero-text{left:32px;top:166px;font-size:10.5px;line-height:17px;color:#555}
.hero-btn{left:31px;top:231px;width:122px;height:38px;background:var(--button);color:var(--white);
  font-family:'Raleway',sans-serif;font-size:12.5px;display:flex;align-items:center;justify-content:center}
.dots{left:357px;top:320px;display:flex;gap:8px}
.dots span{width:8px;height:8px;border:1px solid var(--white)}
.dots .on{background:var(--sky);border-color:var(--sky)}

/* services */
.service{top:520px;width:250px;text-align:center;color:var(--white)}
.service-icon{width:76px;height:76px;margin:0 auto;border:1px solid var(--sky);display:flex;align-items:center;justify-content:center}
.service-icon.filled{background:var(--sky)}
.service h3{font-family:'Raleway',sans-serif;font-weight:400;font-size:17.6px;margin:16px 0 10px}
.service.featured h3{color:var(--sky)}
.service p{font-size:11px;line-height:17px}

/* welcome */
.welcome-title{left:58px;top:768px;font-family:'Raleway',sans-serif;font-weight:400;font-size:24px;color:#111}
.welcome-title span{color:var(--navy)}
.welcome-photo{left:56px;top:810px;width:138px;height:138px;border:6px solid var(--frame);
  background:linear-gradient(160deg,#e9eef2,#b8c2cc 55%,#6d7a86)}
.welcome-text{left:210px;top:811px;width:345px;font-size:10.6px;line-height:16.8px;color:#555}
.quote{left:579px;top:772px;width:245px;height:107px;background:var(--quote-bg);border:1px solid var(--quote-line);border-radius:3px;
  padding:13px 30px;text-align:center;font-size:10.6px;line-height:16.8px;color:#555}
.quote-mark{font-family:'Montserrat',sans-serif;font-size:20px;color:#666}
.quote-tail{left:760px;top:877px}
.author{left:590px;top:906px;width:138px;text-align:right}
.author-name{font-family:'Raleway',sans-serif;font-size:16px;color:#555}
.author-role{font-style:italic;font-size:10.4px;color:#888}
.avatar{left:747px;top:901px;width:46px;height:46px;border-radius:50%;background:radial-gradient(circle at 50% 40%,#d8a982,#7a5a45)}

/* footer */
.site-footer{left:0;top:986px;width:880px;height:168px;background:var(--navy);color:var(--white)}
.footer-heading{font-family:'Raleway',sans-serif;font-weight:400;font-size:16px;top:15px}
.contact-item{left:58px;display:flex;gap:10px;font-size:11px;line-height:17px}
.client{width:112px;height:40px;display:flex;align-items:center;justify-content:center;gap:6px;
  font-family:'Lato',sans-serif;font-size:13px;color:rgba(255,255,255,.75)}
.client i{width:10px;height:10px;border-radius:50%;background:rgba(255,255,255,.5)}
.bottom-bar{left:0;top:1154px;width:880px;height:46px;background:var(--sky)}
.copyright{left:58px;top:16px;font-family:'Raleway',sans-serif;font-size:11px;color:var(--white)}
.copyright span{color:#0b3a66}
.social{left:741px;top:17px;display:flex;gap:13px}
.social span{width:11px;height:11px;border-radius:50%;background:var(--navy)}
</style>
</head>
<body>

<header class="site-header abs">
  <div class="brand abs"><span class="brand-mark"></span><span class="brand-name">Beacon Advisory</span></div>
  <nav class="main-nav abs">
    <span class="active">HOME</span><span>COMPANY</span><span>SERVICES</span><span>SOLUTIONS</span><span>RESOURCES</span><span>CAREER</span><span>CONTACT US</span>
  </nav>
</header>

<div class="band-sky abs"></div>
<div class="band-navy abs"></div>

<section class="hero abs" role="img" aria-label="Smiling businesswoman in an office with colleagues behind her">
  <h1 class="hero-title abs">Beacon Advisory</h1>
  <p class="hero-sub abs">LET YOUR BUSINESS GROW WITH US</p>
  <p class="hero-text abs">Lorem Ipsum is simply dummy text of the printing and typesetting industry.<br>Lorem Ipsum has been the industry's standard.</p>
  <div class="hero-btn abs">CONTACT US</div>
  <div class="dots abs"><span class="on"></span><span></span><span></span><span></span></div>
</section>

<section class="service abs" style="left:53px">
  <div class="service-icon">
    <svg width="36" height="36" viewBox="0 0 36 36" fill="none" stroke="#04a9e2" stroke-width="1.3">
      <circle cx="18" cy="16" r="7"/><path d="M15 23v5h6v-5M15 30h6"/><path d="M18 3v4M6 16h4M26 16h4M9 7l3 3M27 7l-3 3"/>
    </svg>
  </div>
  <h3>Consulting</h3>
  <p>Beacon Advisory has certified professional consultants to work with you to help increase the business by providing IT services...</p>
</section>

<section class="service featured abs" style="left:315px">
  <div class="service-icon filled">
    <svg width="40" height="40" viewBox="0 0 40 40" fill="none" stroke="#fff" stroke-width="1.5">
      <circle cx="17" cy="12" r="6"/><path d="M5 33c0-7 5-11 12-11 2 0 4 .4 5 1"/><path d="M5 33h17"/>
      <circle cx="29" cy="30" r="6"/><path d="M26 30l2 2 4-4"/>
    </svg>
  </div>
  <h3>Staff Augmentation</h3>
  <p>For years Beacon Advisory has been offering our customers the ability to augment their existing staff with temporary highly skilled IT professionals...</p>
</section>

<section class="service abs" style="left:576px">
  <div class="service-icon">
    <svg width="40" height="40" viewBox="0 0 40 40" fill="none" stroke="#04a9e2" stroke-width="1.3">
      <circle cx="20" cy="20" r="15"/><circle cx="20" cy="20" r="8"/><circle cx="20" cy="20" r="3"/>
    </svg>
  </div>
  <h3>Offshore</h3>
  <p>Our Offshore development model has a unique distinction of providing efficient software solutions with cost and quality advantage...</p>
</section>

<h2 class="welcome-title abs">Welcome to <span>Beacon Advisory</span></h2>
<div class="welcome-photo abs" role="img" aria-label="Business team meeting in a bright office"></div>
<p class="welcome-text abs">Lorem Ipsum is simply dummy text of the printing and typesetting industry. Lorem Ipsum has been the industry's standard dummy text ever since the 1500s, when an unknown printer took a galley of type and scrambled it to make a type specimen book. It has survived not only five centuries, but also the leap into electronic typesetting, remaining essentially unchanged. It was popularised in the 1960s with the release of Dryline sheets containing Lorem Ipsum passages, and more recently with desktop publishing software like Folio Layout Studio.</p>

<blockquote class="quote abs">
  <span class="quote-mark abs" style="left:12px;top:4px">"</span>
  Lorem Ipsum is simply dummy text of the printing and typesetting industry. Lorem Ipsum has been the industry's standard dummy text ever since the 1500s.
  <span class="quote-mark abs" style="right:12px;bottom:-4px">"</span>
</blockquote>
<svg class="quote-tail abs" width="20" height="11" viewBox="0 0 20 11"><path d="M0 0L10 10L20 0" fill="#e3f5fc" stroke="#3cb4e6"/><path d="M1 0H19" stroke="#e3f5fc" stroke-width="2"/></svg>
<div class="author abs"><div class="author-name">Martin Halvorsen</div><div class="author-role">Company Name, CEO</div></div>
<div class="avatar abs" role="img" aria-label="Portrait of the reviewer"></div>

<footer class="site-footer abs">
  <h4 class="footer-heading abs" style="left:58px">Contact Info</h4>
  <div class="contact-item abs" style="top:44px">
    <svg width="14" height="20" viewBox="0 0 14 20" fill="none" stroke="#04a9e2" stroke-width="1.3"><path d="M7 19S1 11 1 7a6 6 0 0 1 12 0c0 4-6 12-6 12z"/><circle cx="7" cy="7" r="2.2"/></svg>
    <span>2480 Meridian Rd, Suite 310<br>Fairhaven, NJ 07590</span>
  </div>
  <div class="contact-item abs" style="top:90px">
    <svg width="14" height="16" viewBox="0 0 16 16" fill="none" stroke="#04a9e2" stroke-width="1.3"><path d="M3 1l3 3-2 2c1 2 4 5 6 6l2-2 3 3-2 2C7 15 1 9 1 3z"/></svg>
    <span>+1 (555) 318 2047</span>
  </div>
  <div class="contact-item abs" style="top:120px">
    <svg width="14" height="14" viewBox="0 0 16 12" fill="none" stroke="#04a9e2" stroke-width="1.3"><rect x="1" y="1" width="14" height="10"/><path d="M1 1l7 6 7-6"/></svg>
    <span>info@beaconadvisory.com</span>
  </div>

  <h4 class="footer-heading abs" style="left:319px">Clients</h4>
  <div class="client abs" style="left:316px;top:42px"><i></i>Vigilens</div>
  <div class="client abs" style="left:438px;top:42px"><i></i>Corvex Labs</div>
  <div class="client abs" style="left:560px;top:42px"><i></i>Harrow Secure</div>
  <div class="client abs" style="left:680px;top:42px"><i></i>Nimbus Cloud</div>
  <div class="client abs" style="left:316px;top:104px"><i></i>Vigilens</div>
  <div class="client abs" style="left:438px;top:104px"><i></i>Corvex Labs</div>
  <div class="client abs" style="left:560px;top:104px"><i></i>Harrow Secure</div>
  <div class="client abs" style="left:680px;top:104px"><i></i>Nimbus Cloud</div>
</footer>

<div class="bottom-bar abs">
  <p class="copyright abs">© <span>Beacon Advisory</span> 2016. All Rights Reserved</p>
  <div class="social abs"><span></span><span></span><span></span><span></span></div>
</div>

</body>
</html>
```